Personal Injury Law Firm needs folder design

Need a folder design for our personal injury law firm, Corrow & Talmidge, LLC. to give to all of our clients with their documents at the end of their case. I've attached our branding guide. We are branded as the 5 star law firm that fights for our clients like family. It should incorporate our colors or Green and White. We'd like to convey a message of moving on to the next chapter after finishing their case.

```html
<!DOCTYPE html>
<html lang="en">
<head>
<meta charset="utf-8">
<title>Corrow &amp; Talmidge, LLC. — Client Folder</title>
<link rel="stylesheet" href="https://fonts.googleapis.com/css2?family=Cinzel:wght@500&family=Lato:wght@400&display=swap">
<style>
  :root {
    --backdrop: #7b8482;
    --paper: #ffffff;
    --paper-shade: #ececec;
    --brand-green: #1a9060;
    --link-green: #23a873;
    --ink: #2b2f2e;
    --crease: #dcdcdc;
  }
  * { margin: 0; padding: 0; box-sizing: border-box; }
  html, body {
    width: 1200px;
    height: 900px;
    overflow: hidden;
    background: var(--backdrop);
  }
  .folder-spread {
    position: absolute;
    left: 80px;
    top: 100px;
    width: 1040px;
    height: 700px;
    display: flex;
    box-shadow: 0 18px 40px rgba(0, 0, 0, 0.25);
  }
  .folder-panel {
    position: relative;
    width: 520px;
    height: 700px;
    background: linear-gradient(160deg, var(--paper) 0%, #f7f7f7 55%, var(--paper-shade) 100%);
  }
  .folder-panel--back { border-right: 1px solid var(--crease); }
  .panel-texture {
    position: absolute;
    inset: 0;
    background: radial-gradient(ellipse at 40% 40%, rgba(255,255,255,0.9), rgba(236,236,236,0.5));
  }
  .website {
    position: absolute;
    left: 0;
    right: 0;
    bottom: 110px;
    text-align: center;
    font-family: "Lato", sans-serif;
    font-size: 15px;
    letter-spacing: 2px;
    color: var(--link-green);
  }
  .firm-mark {
    position: absolute;
    left: 110px;
    top: 200px;
    display: flex;
    align-items: center;
    gap: 12px;
  }
  .firm-mark__square {
    width: 44px;
    height: 44px;
    background: var(--brand-green);
    flex: none;
  }
  .firm-mark__name {
    font-family: "Cinzel", serif;
    font-weight: 500;
    font-size: 22px;
    color: var(--brand-green);
    line-height: 1.1;
  }
  .firm-mark__practice {
    font-family: "Cinzel", serif;
    font-weight: 500;
    font-size: 9px;
    letter-spacing: 3px;
    color: var(--ink);
    margin-top: 4px;
  }
</style>
</head>
<body>
  <main class="folder-spread">
    <section class="folder-panel folder-panel--back">
      <div class="panel-texture" role="img" aria-label="Faint pattern of soft rounded squares across the back cover"></div>
      <p class="website">www.corrowandtalmidge.com</p>
    </section>
    <section class="folder-panel folder-panel--front">
      <div class="panel-texture" role="img" aria-label="Faint pattern of soft rounded squares across the front cover"></div>
      <div class="firm-mark">
        <span class="firm-mark__square"></span>
        <div>
          <p class="firm-mark__name">Corrow &amp; Talmidge, LLC.</p>
          <p class="firm-mark__practice">INJURY ATTORNEYS</p>
        </div>
      </div>
    </section>
  </main>
</body>
</html>
```